Orvane Mechanical - Letterhead

We are a plumbing and hvac company based in Calgary. This letterhead will be on our quotes, invoices, preventative maintenance proposals etc.

```html
<!DOCTYPE html>
<html lang="en">
<head>
<meta charset="utf-8">
<title>Orvane Mechanical – Letterhead</title>
<link rel="stylesheet" href="https://fonts.googleapis.com/css2?family=Encode+Sans+Semi+Condensed:wght@300;400;700&family=Lato:wght@400;700&display=swap">
<style>
  :root {
    --brand-blue: #1e6bb8;
    --brand-orange: #f15a24;
    --body-text: #5a5a5a;
    --paper: #ffffff;
  }
  html, body {
    margin: 0;
    padding: 0;
    width: 1056px;
    height: 1200px;
    overflow: hidden;
    background: var(--paper);
  }
  .letterhead {
    position: relative;
    width: 1056px;
    height: 1200px;
    background: var(--paper);
    font-family: "Encode Sans Semi Condensed", "Arial Narrow", sans-serif;
    color: var(--body-text);
  }
  .brand-mark {
    position: absolute;
    top: 112px;
    left: 0;
    width: 1056px;
    display: flex;
    justify-content: center;
    align-items: center;
    gap: 14px;
  }
  .brand-dot {
    width: 30px;
    height: 30px;
    border-radius: 50%;
    background: var(--brand-orange);
  }
  .brand-name {
    font-family: "Encode Sans Semi Condensed", "Arial Narrow", sans-serif;
    font-weight: 700;
    font-size: 44px;
    letter-spacing: 0.02em;
    color: var(--brand-blue);
    text-transform: uppercase;
  }
  .letter-body p {
    position: absolute;
    left: 97px;
    width: 858px;
    margin: 0;
    font-size: 19px;
    font-weight: 300;
    line-height: 29.5px;
    text-align: justify;
  }
  .salutation { top: 338px; }
  .para-one { top: 393px; }
  .para-two { top: 540px; }
  .para-three { top: 658px; }
  .para-four { top: 775px; }
  .closing { top: 939px; }
  .signature {
    position: absolute;
    left: 94px;
    top: 982px;
    width: 86px;
    height: 44px;
    background: linear-gradient(90deg, rgba(241, 90, 36, 0.18), rgba(241, 90, 36, 0.06));
    border-radius: 4px;
  }
  .footer-title {
    position: absolute;
    top: 1119px;
    left: 83px;
    width: 902px;
    display: flex;
    align-items: center;
    gap: 14px;
  }
  .footer-rule {
    flex: 1;
    height: 1.5px;
    background: var(--brand-orange);
  }
  .footer-name {
    font-family: "Lato", sans-serif;
    font-weight: 700;
    font-size: 15px;
    letter-spacing: 0.32em;
    color: var(--brand-orange);
    text-transform: uppercase;
    white-space: nowrap;
  }
  .footer-contacts {
    position: absolute;
    top: 1146px;
    left: 0;
    width: 1056px;
    text-align: center;
    font-family: "Lato", sans-serif;
    font-size: 14.5px;
    color: var(--brand-blue);
    white-space: nowrap;
  }
  .footer-contacts .sep { margin: 0 7px; }
</style>
</head>
<body>
<main class="letterhead">
  <header class="brand-mark">
    <span class="brand-dot"></span>
    <span class="brand-name">Orvane Mechanical</span>
  </header>

  <section class="letter-body">
    <p class="salutation">Dear Sir/Mam,</p>
    <p class="para-one">Contrary to popular belief, Lorem Ipsum is not simply random text. It has roots in a piece of classical Latin literature from 45 BC, making it over 2000 years old. Dorian Halbrook, a Latin professor at Westmere College in Virginia, looked up one of the more obscure Latin words, consectetur.</p>
    <p class="para-two">Lorem Ipsum comes from sections 1.10.32 and 1.10.33 of "de Finibus Bonorum et Malorum" (The Extremes of Good and Evil) by Aurelian Tesk, written in 45 BC. This book is a treatise on the theory of ethics, very popular during the Renaissance. The first line of Lorem Ipsum.</p>
    <p class="para-three">The standard chunk of Lorem Ipsum used since the 1500s is reproduced below for those interested. Sections 1.10.32 and 1.10.33 from "de Finibus Bonorum et Malorum" by Aurelian Tesk are also reproduced in their exact original.</p>
    <p class="para-four">The standard chunk of Lorem Ipsum used since the 1500s is reproduced below for those interested.</p>
    <p class="closing">Best Regards</p>
    <div class="signature" role="img" aria-label="Handwritten signature of the sender"></div>
  </section>

  <footer>
    <div class="footer-title">
      <span class="footer-rule"></span>
      <span class="footer-name">Orvane Mechanical Inc</span>
      <span class="footer-rule"></span>
    </div>
    <div class="footer-contacts">
      403-555-0187<span class="sep">|</span>hello@orvanemech.ca<span class="sep">|</span>www.orvanemech.ca<span class="sep">|</span>1420 Kelvin Avenue SE #210 Calgary, AB T2G 0A0
    </div>
  </footer>
</main>
</body>
</html>
```